Holistic/ Sports Psychologist needs flyer design

I need a flyer designed that catches the attention of potential customers - (parents of young athletes and athletes) who may be looking for psychological services. I have a logo and all the relevant info for the flyer but would like someone to take it and make it look creative, fun, fresh and attention getting for high school and college athletes. The colors used can be from my logo design which represents my holistic approach.
Target Market(s)
high school and collegiate athletes
Industry/Entity Type
sports psychology
Requirements
Must have
- Info I put on the flyer with my logo and please add some graphics and color based on my logo

```html
<!DOCTYPE html>
<html lang="en">
<head>
<meta charset="UTF-8">
<title>Holistic Psychology Flyer</title>
<link href="https://fonts.googleapis.com/css2?family=Outfit:wght@300;400;500;600;700;800&display=swap" rel="stylesheet">
<style>
  :root {
    --blue: #356a9e;
    --green: #a8d177;
    --green-soft: #d7eac0;
    --panel: #e8f0f7;
    --ink: #2b2b2b;
    --text: #333333;
    --white: #ffffff;
    --stage: #e4e6e8;
  }
  * { margin: 0; padding: 0; box-sizing: border-box; }
  html, body { width: 1017px; height: 1200px; overflow: hidden; }
  body {
    background: var(--stage);
    font-family: "Outfit", sans-serif;
    color: var(--text);
    position: relative;
  }
  .flyer {
    position: absolute;
    left: 98px; top: 20px;
    width: 820px; height: 1160px;
    background: var(--white);
    overflow: hidden;
  }
  .flyer-art { position: absolute; inset: 0; }
  .abs { position: absolute; }

  .brand-name {
    left: 190px; top: 92px;
    font-size: 34px; font-weight: 400; color: var(--blue);
    letter-spacing: 0.5px; white-space: nowrap;
  }

  .telehealth-lead {
    left: 545px; top: 208px;
    font-size: 18px; line-height: 15px; color: var(--ink); font-weight: 400;
  }
  .telehealth-word {
    left: 543px; top: 242px;
    font-size: 45px; font-weight: 800; color: var(--ink); line-height: 1; letter-spacing: -0.5px;
  }
  .session-note {
    right: 110px; top: 322px; text-align: right;
    font-size: 15px; line-height: 17px; color: var(--ink);
  }
  .session-note strong { font-weight: 700; font-size: 17px; }

  .title {
    left: 66px; top: 298px;
    font-weight: 800; color: var(--blue);
    font-size: 70px; line-height: 66px; letter-spacing: -1px;
  }
  .subtitle {
    left: 68px; top: 442px;
    font-size: 31px; font-weight: 700; color: var(--blue); white-space: nowrap;
  }

  .ways {
    left: 69px; top: 516px; width: 700px;
  }
  .ways h2 {
    font-size: 26px; font-weight: 700; color: var(--ink); line-height: 28px;
    letter-spacing: -0.3px; margin-bottom: 18px;
  }
  .ways ul { list-style: none; }
  .ways li { position: relative; padding-left: 18px; margin-bottom: 11px; }
  .ways li::before {
    content: ""; position: absolute; left: 1px; top: 3px;
    width: 3px; height: 11px; background: var(--blue); transform: skewX(-35deg);
  }
  .ways h3 { font-size: 13.5px; font-weight: 700; color: var(--ink); line-height: 15px; }
  .ways p { font-size: 12.5px; font-weight: 400; line-height: 15px; color: var(--text); }

  .section-tag {
    left: 69px; top: 852px; width: 187px; height: 32px;
    background: var(--blue); color: var(--white);
    font-size: 21px; font-weight: 700; line-height: 32px; padding-left: 46px;
  }
  .bio {
    left: 69px; top: 901px; width: 665px;
    font-size: 12.5px; line-height: 15px; color: var(--text);
  }
  .bio p + p { margin-top: 14px; }
  .bio .narrow { width: 480px; }
  .bio strong { font-weight: 700; color: var(--ink); }

  .address {
    left: 66px; top: 1076px;
    font-size: 18px; font-weight: 700; color: var(--white); line-height: 21px;
  }
  .web {
    right: 66px; top: 1064px;
    font-size: 14px; letter-spacing: 2.5px; color: var(--white);
  }
  .phone {
    right: 66px; top: 1085px;
    font-size: 29px; font-weight: 800; color: var(--white); display: flex; align-items: center; gap: 10px;
  }
</style>
</head>
<body>
<main class="flyer">
  <svg class="flyer-art" width="820" height="1160" viewBox="0 0 820 1160">
    <!-- top-right cloud -->
    <path d="M574 0 C585 55 640 70 690 22 C690 80 750 125 820 124 V0 Z" fill="var(--green-soft)"/>
    <!-- brand circle and band -->
    <circle cx="112" cy="123" r="60" fill="none" stroke="var(--blue)" stroke-width="4"/>
    <rect x="180" y="134" width="445" height="31" fill="var(--green)"/>
    <!-- soft burst behind title -->
    <polygon points="95,279 104,315 150,300 118,330 145,372 100,350 70,387 72,345 38,330 74,316" fill="var(--green-soft)" opacity="0.8"/>
    <!-- monitor icon -->
    <g fill="none" stroke="var(--ink)" stroke-width="4" stroke-linejoin="round">
      <rect x="440" y="213" width="74" height="58" rx="5"/>
      <line x1="476" y1="271" x2="476" y2="285"/>
      <line x1="460" y1="287" x2="492" y2="287"/>
      <path d="M460 242 h8 l5 -10 l6 18 l5 -8 h10"/>
      <path d="M462 232 c0 -10 14 -12 15 -2 c1 -10 15 -8 15 2 c0 8 -8 14 -15 20 c-7 -6 -15 -12 -15 -20"/>
      <path d="M520 230 v40 a6 6 0 0 1 -6 6" stroke-dasharray="3 3"/>
    </g>
    <!-- stopwatch icon -->
    <g stroke="var(--ink)" stroke-width="4" fill="none">
      <circle cx="738" cy="342" r="19"/>
      <line x1="738" y1="319" x2="738" y2="323"/>
      <line x1="731" y1="318" x2="745" y2="318"/>
      <line x1="754" y1="325" x2="758" y2="321"/>
    </g>
    <path d="M738 342 V328 A14 14 0 1 1 724 342 Z" fill="var(--ink)"/>
    <!-- lower panel -->
    <rect x="0" y="491" width="820" height="669" fill="var(--panel)"/>
    <!-- section tag green slant -->
    <polygon points="69,852 106,852 84,884 69,884" fill="var(--green)"/>
    <!-- footer waves -->
    <path d="M0 1035 Q 500 1070 820 862 V1160 H0 Z" fill="var(--green)"/>
    <path d="M0 1046 Q 520 1080 820 946 V1160 H0 Z" fill="var(--blue)"/>
    <!-- phone icon -->
    <rect x="521" y="1093" width="12" height="20" rx="2" fill="none" stroke="var(--green)" stroke-width="2"/>
  </svg>

  <div class="abs brand-name">Dr. Elena Whitford</div>

  <div class="abs telehealth-lead">All services are provided<br>online via</div>
  <div class="abs telehealth-word">telehealth</div>

  <div class="abs session-note">Sessions are<br><strong>30 or 55 minutes</strong></div>

  <h1 class="abs title">Holistic<br>Psychology</h1>
  <div class="abs subtitle">and sports Psychology Consulting</div>

  <section class="abs ways">
    <h2>Ways to Improve Athletic Performance Using Sports and Holistic Psychology</h2>
    <ul>
      <li><h3>MENTAL SKILLS TRAINING</h3><p>Ex: visualization, goal-setting, motivation, self- talk, mindset, concentration techniques.</p></li>
      <li><h3>PERFORMANCE ENHANCEMENT</h3><p>Eliminate psychological barriers that are hindering performance such as self- doubt, perfectionism, fear of failure, and burnout.</p></li>
      <li><h3>MENTAL HEALTH</h3><p>Anxiety and stress management by using relaxation techniques, breathwork, and mindfulness practices.</p></li>
      <li><h3>INJURY RECOVERY SUPPORT</h3><p>Assist athletes in maintaining resilience and positive mental attitude during rehabilitation as well as processing emotions relating to any potential trauma caused by the injury or life transitions resulting from it.</p></li>
      <li><h3>BURNOUT PREVENTION</h3><p>Teach athletes how to have balance in sports and life so they can experience longevity in their sports as well as overall optimal health and well-being.</p></li>
    </ul>
  </section>

  <div class="abs section-tag">Background</div>
  <div class="abs bio">
    <p><strong>Dr. Elena Whitford</strong> is a licensed psychologist. She understands the unique experiences of athletes due to her background as an All-American swimmer, collegiate and age group swim coach, parent of a collegiate/professional athlete, and sports psychology researcher. She works with athletes to optimize performance and overall well-being.</p>
    <p class="narrow">Her specializations include: performance anxiety, mental performance, stress management, anxiety, depressions, trauma, life transitions, relationship issues, injury, and sleep.</p>
  </div>

  <address class="abs address" style="font-style:normal">2208 Harbor Lane #104<br>Cedar Point, FL 32099</address>
  <div class="abs web">drelenawhitford.com</div>
  <div class="abs phone">555-014-2290</div>
</main>
</body>
</html>
```